Modern card design needed for building development company

We are looking for a sharp modern new look for our business cards.
We are a New Zealand based company called TKR Ventures NZ LTD that specialises in subdividing large sections, housing and commercial buildings.
We have attached a photo of the current logo and would like to see it improved somehow as it looks a bit dated.
We are open to any colours.

Target Market(s)

Investors, Property buyers

Industry/Entity Type

Investment

Contact Information for Business Card

TKR VENTURES NZ LTD
www.tkrventuresnz.co.nz

Damon Whitcombe
Phone +64 21 938 104
Email dpwhitcombe@korumail.co.nz

Font styles to use
Serif
Sans Serif

Colors
0792cd
33a6d7
85cae6
6b449b
886aae
f04a50
ec1f27
f37122
f68d4d

Requirements
Must have
• Please try and make the logo more modern or if you have a similar one we would like to see it.

```html
<!DOCTYPE html>
<html lang="en">
<head>
<meta charset="utf-8">
<title>TKR Ventures NZ LTD — Business Cards</title>
<link href="https://fonts.googleapis.com/css2?family=Jost:wght@400;500&display=swap" rel="stylesheet">
<style>
  :root {
    --bg: #d9dbda;
    --card: #ffffff;
    --accent: #9b1c2c;
    --ink: #2a2a2a;
    --muted: #555759;
  }
  * { box-sizing: border-box; margin: 0; padding: 0; }
  html, body { width: 1200px; height: 904px; overflow: hidden; }
  body {
    background: var(--bg);
    font-family: "Jost", "Futura", sans-serif;
    color: var(--ink);
    position: relative;
  }
  .card {
    position: absolute;
    width: 560px;
    height: 320px;
    background: var(--card);
    box-shadow: 0 6px 18px rgba(0,0,0,0.18);
  }
  .card--front { left: 120px; top: 90px; }
  .card--back  { left: 520px; top: 494px; }

  .brand {
    display: flex;
    align-items: center;
    gap: 10px;
    font-weight: 400;
    color: var(--muted);
    letter-spacing: 0.06em;
  }
  .brand__mark {
    width: 14px; height: 14px;
    background: var(--accent);
  }
  .card--front .brand {
    position: absolute;
    left: 0; right: 0; top: 130px;
    justify-content: center;
    font-size: 26px;
  }
  .web-line {
    position: absolute;
    left: 0; right: 0; bottom: 44px;
    text-align: center;
    font-size: 15px;
    color: var(--ink);
    letter-spacing: 0.02em;
  }
  .web-line__domain { color: var(--accent); }

  .card--back .brand {
    position: absolute;
    right: 34px; top: 40px;
    font-size: 17px;
  }
  .side-bar {
    position: absolute;
    left: 0; top: 110px;
    width: 18px; height: 40px;
    background: var(--accent);
  }
  .person {
    position: absolute;
    left: 46px; top: 90px;
  }
  .person__name { font-size: 25px; font-weight: 500; line-height: 1.1; }
  .person__role { font-size: 18px; color: var(--accent); }

  .address {
    position: absolute;
    right: 34px; top: 118px;
    text-align: right;
    font-size: 15px;
    line-height: 1.3;
  }
  .contacts {
    position: absolute;
    left: 46px; bottom: 30px;
    list-style: none;
    font-size: 15px;
    line-height: 1.45;
  }
  .contacts li { display: flex; align-items: center; gap: 12px; }
  .contacts svg { width: 14px; height: 14px; flex: none; }
</style>
</head>
<body>

  <section class="card card--front" aria-label="Card front">
    <div class="brand"><span class="brand__mark"></span>TKR VENTURES NZ LTD</div>
    <p class="web-line">www.<span class="web-line__domain">tkrventuresnz</span>.co.nz</p>
  </section>

  <section class="card card--back" aria-label="Card back">
    <div class="brand"><span class="brand__mark"></span>TKR VENTURES NZ LTD</div>
    <span class="side-bar"></span>
    <div class="person">
      <h1 class="person__name">Damon Whitcombe</h1>
      <p class="person__role">Founder/CEO</p>
    </div>
    <address class="address" style="font-style:normal">
      Address:<br>Your Street Address,<br>New Zealand, 1234
    </address>
    <ul class="contacts">
      <li>
        <svg viewBox="0 0 16 16" aria-hidden="true"><path d="M4 1.5l2.5 3-1.5 1.5c.8 1.8 2.2 3.2 4 4l1.5-1.5 3 2.5-1.5 2.5C6.5 13.5 2.5 9.5 1.5 3z" fill="var(--accent)"/></svg>
        +64 21 938 104
      </li>
      <li>
        <svg viewBox="0 0 16 16" aria-hidden="true"><rect x="1.5" y="3.5" width="13" height="9" fill="none" stroke="var(--accent)" stroke-width="1.5"/><path d="M1.5 3.5L8 9l6.5-5.5" fill="none" stroke="var(--accent)" stroke-width="1.5"/></svg>
        dpwhitcombe@korumail.co.nz
      </li>
      <li>
        <svg viewBox="0 0 16 16" aria-hidden="true"><g fill="none" stroke="var(--accent)" stroke-width="1.2"><circle cx="8" cy="8" r="6.5"/><ellipse cx="8" cy="8" rx="3" ry="6.5"/><path d="M1.5 8h13M2.5 5h11M2.5 11h11"/></g></svg>
        <span>www.<span class="web-line__domain">tkrventuresnz</span>.co.nz</span>
      </li>
    </ul>
  </section>

</body>
</html>
```